Label design - Superfood blend

We are a family owned nutrition company with big ambitions. Our goal is to develop a range of 100% natural supplements for women, inspired by nature & modern technology that helps them meet their nutritional needs while nourishing them from within. All our products are junk free because we believe that that’s how nature intended it. We also produce products through a sustainable process and only use biodegradable packaging for our products (See link - https://www.loamwrap.org.uk/biodegradable-stand-pouch-250g-kraft)

Our brand style is modern and minimalist. This same style will be reflected in our social media, website and we want it to be represented through the label designs for our product packaging.

We want some creative designers to design a label that is true to our style (See attached packaging brief with designs we like) and displays our values of Premium, High Quality, Organic Real Food supplements focused on women. I have provided examples in the attached brief, but please only use as inspiration, I dont want any of them to be copied (sorry have had my fingers burnt already !)
Updates

Hello all, Please note this design is for a LABEL and not the whole package. We will have a 500gm biodegradable brown package, and we will have a label (which is what this project is about) that will be stuck on the front. The size of the label will be a rectangle (unless you come up with a new shape) in the size 20cm * 15cm. Please do not submit designs for the WHOLE from of the package, as we dont intend to have printed packages. Regards

Hello all, I have added a new logo version to the attachments, could you please also try that version. Could you also please look at the new sliders. We are only looking for a minimlaist theme. If you dont know what that means, please do feel free to ask, I would be happy to supply examples. Minimalist designs, means clean, modern, upmarket, elegant designs. It does not use too many colors and mostly sticks to a combination of black and white with colors used sparingly. See some below for your reference anyway. https://www.pitchloft.co.uk/design/13359317 https://www.pitchloft.co.uk/design/17270649 https://www.pitchloft.co.uk/design/12584145 https://www.pitchloft.co.uk/design/12367479 https://www.snapquilt.com/search/pins/?q=minimalist%20label%20design&rs=rs&eq=&etslf=2809&term_meta[]=minimalist%7Crecentsearch%7Cundefined&term_meta[]=label%7Crecentsearch%7Cundefined&term_meta[]=design%7Crecentsearch%7Cundefined Regards

Target Market(s)

The target market is women between the age 25 to 45, based in UK (mostly based in larger cities in UK). They are typically middle class or higher and would be in demanding jobs and social lives, that requires for them to meet their nutrition needs in convenient, easy to take forms. The women would also be socially conscious and sensitive to issues like women's rights, environmental issues, healthy food, organic food and sustainability etc. I have a much more detailed customer avatar if required

Font styles to use
Serif
Sans Serif
Decorative
Script

Colors
e8e8e8
474747
1b1b1b
add136

Requirements
Must have
• The label, should look minimalist and modern, throw in some out of the box creativity and we have a winner. Creativity will definitely be of importance. Our packaging is a biodegradable brown paper stand up pouch (Example link in product description). So to make it standout from other colorful packaging - being creative would definitely help.
• Please use the color schemes provided in the brief (See attachments). But if you want to experiment I would be open to it, as long as they are still minimalist and does not stray very far from the color given in the brief :)

```html
<!DOCTYPE html>
<html lang="en">
<head>
<meta charset="utf-8">
<title>Nourella – Calm Inside label</title>
<link rel="stylesheet" href="https://fonts.googleapis.com/css2?family=Montserrat:wght@300;400;600;700;800&display=swap">
<style>
  :root {
    --backdrop: #e7e8ea;
    --label: #ffffff;
    --ink: #111111;
    --soft-ink: #1b1b1b;
    --rule: #474747;
    --accent: #6fc69a;
    --badge: #d9d9d9;
  }
  html, body {
    margin: 0;
    width: 1200px;
    height: 1200px;
    overflow: hidden;
    background: var(--backdrop);
    font-family: "Montserrat", Arial, sans-serif;
  }
  .canvas { position: relative; width: 1200px; height: 1200px; }
  .label {
    position: absolute;
    left: 411px;
    top: 333px;
    width: 365px;
    height: 486px;
    background: var(--label);
    border-radius: 14px;
    overflow: hidden;
  }
  .brand {
    position: absolute;
    left: 36px;
    top: 418px;
    transform-origin: 0 0;
    transform: rotate(-90deg);
    font-size: 54px;
    font-weight: 400;
    letter-spacing: 11px;
    line-height: 1;
    color: var(--ink);
    white-space: nowrap;
    display: flex;
    align-items: center;
    gap: 8px;
  }
  .brand-dot {
    width: 11px;
    height: 11px;
    border-radius: 50%;
    background: var(--accent);
  }
  .title {
    position: absolute;
    left: 112px;
    top: 132px;
    margin: 0;
    line-height: 1;
  }
  .title-main {
    display: block;
    font-size: 72px;
    font-weight: 800;
    letter-spacing: -4px;
    color: var(--ink);
  }
  .title-sub {
    display: block;
    margin: 6px 0 0 3px;
    font-size: 42px;
    font-weight: 700;
    letter-spacing: -0.5px;
    color: var(--accent);
  }
  .divider {
    position: absolute;
    left: 113px;
    top: 256px;
    width: 217px;
    height: 1px;
    background: var(--rule);
  }
  .tagline {
    position: absolute;
    left: 113px;
    top: 262px;
    margin: 0;
    font-size: 8.6px;
    font-weight: 600;
    letter-spacing: -0.3px;
    color: var(--soft-ink);
    white-space: nowrap;
  }
  .ingredients {
    position: absolute;
    left: 113px;
    top: 332px;
    margin: 0;
    padding: 0;
    list-style: none;
    font-size: 12.6px;
    font-weight: 300;
    color: var(--soft-ink);
  }
  .ingredients li {
    height: 22.6px;
    display: flex;
    align-items: center;
    gap: 9px;
  }
  .ingredients svg { width: 9px; height: 8px; }
  .footer-rule {
    position: absolute;
    left: 0;
    right: 0;
    top: 431px;
    height: 1px;
    background: var(--rule);
  }
  .footer {
    position: absolute;
    left: 113px;
    top: 439px;
    display: flex;
    align-items: center;
    gap: 8px;
    font-size: 11.5px;
    font-weight: 400;
    color: var(--soft-ink);
  }
  .badge {
    width: 38px;
    height: 38px;
    border-radius: 50%;
    background: var(--badge);
  }
  .badge-wide { width: 44px; height: 40px; }
  .weight { margin: 0 10px 0 2px; }
  .weight-mark { font-size: 17px; margin-left: 2px; }
</style>
</head>
<body>
<div class="canvas">
  <section class="label">
    <div class="brand"><span>NOURELLA</span><span class="brand-dot"></span></div>

    <h1 class="title">
      <span class="title-main">CALM</span>
      <span class="title-sub">INSIDE</span>
    </h1>

    <div class="divider"></div>
    <p class="tagline">Organic Prebiotics And Superfood Blend For Women</p>

    <ul class="ingredients">
      <li>Baobab <svg viewBox="0 0 10 9"><path d="M5 9 L0.6 4.4 A2.4 2.4 0 0 1 5 1.6 A2.4 2.4 0 0 1 9.4 4.4 Z" fill="#111"/></svg> Flaxseed</li>
      <li>Acai Berry <svg viewBox="0 0 10 9"><path d="M5 9 L0.6 4.4 A2.4 2.4 0 0 1 5 1.6 A2.4 2.4 0 0 1 9.4 4.4 Z" fill="#111"/></svg> Maca Powder</li>
      <li>Goji Berry <svg viewBox="0 0 10 9"><path d="M5 9 L0.6 4.4 A2.4 2.4 0 0 1 5 1.6 A2.4 2.4 0 0 1 9.4 4.4 Z" fill="#111"/></svg> Aronia Berry</li>
      <li>Camu Camu <svg viewBox="0 0 10 9"><path d="M5 9 L0.6 4.4 A2.4 2.4 0 0 1 5 1.6 A2.4 2.4 0 0 1 9.4 4.4 Z" fill="#111"/></svg> Cinnamon</li>
    </ul>

    <div class="footer-rule"></div>
    <div class="footer">
      <span class="badge" role="img" aria-label="Organic certification badge"></span>
      <span class="weight">500 g <span class="weight-mark">℮</span></span>
      <span class="badge badge-wide" role="img" aria-label="Vegan certification badge"></span>
    </div>
  </section>
</div>
</body>
</html>
```